Banner ads for LP that work with same theme as below banners

Love the banner ads below. Need more with attached photos. But use the same wording, font as in below banner ads. Should be LP size 1200/627 so I can use for Pixorly and LP. Looking for great ads to use as LP ads. We do lots of ads so it will be worth your time to enter this contest you will be rewarded with a ton of work. Need several banner ads that work together. So maybe 1 of the dresses, 1 of the sweater, 1 of the leggings, 1 of the jacket

Target Market(s)

Women 24-45

Industry/Entity Type

Fashion

Requirements
Must have
• Banner ads that work for LP and Pixorly
Nice to have
• Several options to choose from
Should not have
• not sure

```html
<!DOCTYPE html>
<html lang="en">
<head>
<meta charset="utf-8">
<title>Our Best Leggings Ever – Banner</title>
<link rel="stylesheet" href="https://fonts.googleapis.com/css2?family=Kaushan+Script&family=Tinos:wght@400;700&display=swap">
<style>
  :root {
    --ink-black: #0b0b0c;
    --charcoal: #1f1f22;
    --slate-band: #45435a;
    --slate-deep: #34334a;
    --floor: #d7d3c3;
    --floor-shade: #58585c;
    --legging-navy: #2b2f45;
    --skin: #d9a48a;
    --white: #ffffff;
    --button-ink: #141414;
  }
  html, body {
    margin: 0;
    padding: 0;
    width: 1200px;
    height: 627px;
    overflow: hidden;
    background: var(--charcoal);
  }
  .banner {
    position: relative;
    width: 1200px;
    height: 627px;
    overflow: hidden;
  }
  .backdrop {
    position: absolute;
    inset: 0;
  }
  .headline {
    position: absolute;
    left: 0;
    top: 0;
    width: 1200px;
    height: 627px;
    margin: 0;
    color: var(--white);
    font-weight: 400;
  }
  .headline span { position: absolute; white-space: nowrap; }
  .headline-script {
    font-family: "Kaushan Script", cursive;
  }
  .headline-lead {
    left: 478px;
    top: 112px;
    font-size: 62px;
    line-height: 1;
  }
  .headline-product {
    left: 420px;
    top: 208px;
    font-family: "Tinos", serif;
    font-size: 62px;
    letter-spacing: 0.33em;
    line-height: 1;
  }
  .headline-close {
    left: 505px;
    top: 298px;
    font-size: 72px;
    line-height: 1;
  }
  .cta {
    position: absolute;
    left: 512px;
    top: 530px;
    width: 384px;
    height: 64px;
    background: var(--slate-band);
    box-shadow: inset 0 0 0 2px rgba(255,255,255,0.35);
    display: flex;
    align-items: center;
    justify-content: center;
    font-family: "Tinos", serif;
    font-size: 36px;
    color: var(--button-ink);
    text-decoration: none;
    letter-spacing: 0.01em;
  }
  .cta strong { font-weight: 700; }
  .cta .cta-light { font-weight: 400; margin: 0 0.25em; }
</style>
</head>
<body>
<main class="banner">
  <svg class="backdrop" width="1200" height="627" viewBox="0 0 1200 627" xmlns="http://www.w3.org/2000/svg">
    <defs>
      <linearGradient id="sky" x1="0" y1="0" x2="0" y2="1">
        <stop offset="0" stop-color="#2a2a2d"/>
        <stop offset="1" stop-color="#121214"/>
      </linearGradient>
      <radialGradient id="glow-left" cx="0.5" cy="0.5" r="0.5">
        <stop offset="0" stop-color="#cfe4ff" stop-opacity="0.9"/>
        <stop offset="1" stop-color="#3a5c8a" stop-opacity="0"/>
      </radialGradient>
      <radialGradient id="glow-right" cx="0.5" cy="0.5" r="0.5">
        <stop offset="0" stop-color="#dbe9ff" stop-opacity="0.9"/>
        <stop offset="1" stop-color="#4d6a99" stop-opacity="0"/>
      </radialGradient>
      <linearGradient id="legging-tone" x1="0" y1="0" x2="1" y2="1">
        <stop offset="0" stop-color="#3a3f58"/>
        <stop offset="0.6" stop-color="var(--legging-navy)"/>
        <stop offset="1" stop-color="#c79a85"/>
      </linearGradient>
    </defs>

    <rect class="sky" width="1200" height="627" fill="url(#sky)"/>
    <ellipse cx="40" cy="318" rx="120" ry="36" fill="url(#glow-left)"/>
    <ellipse cx="1160" cy="50" rx="110" ry="34" fill="url(#glow-right)"/>

    <polygon class="floor" points="0,470 1200,420 1200,627 0,627" fill="var(--floor)"/>
    <polygon class="floor-shade" points="0,540 430,627 0,627" fill="var(--floor-shade)"/>

    <rect class="model-photo model-photo--right" x="885" y="0" width="190" height="627" rx="30"
          fill="url(#legging-tone)" role="img" aria-label="Photo of a model's legs wearing navy leggings with white lace bands, seen from the front"/>

    <polygon class="band band--slate" points="0,150 1200,90 1200,180 0,215" fill="var(--slate-band)"/>
    <polygon class="band band--black" points="0,215 1200,180 1200,420 0,470" fill="var(--ink-black)"/>

    <rect class="model-photo model-photo--left" x="60" y="0" width="280" height="575" rx="40"
          fill="url(#legging-tone)" role="img" aria-label="Photo of a model's legs in navy leggings with white lace bands, mid jump with crossed feet"/>
  </svg>

  <h1 class="headline">
    <span class="headline-script headline-lead">Our Best</span>
    <span class="headline-product">LEGGINGS</span>
    <span class="headline-script headline-close">Ever!</span>
  </h1>

  <a class="cta" href="#"><strong>SHOP</strong><span class="cta-light">THE</span><strong>LOOK</strong></a>
</main>
</body>
</html>
```